BrivoTerna. Lantern of the Steady Harvest. Business card

Professional business card for BrivoTerna (Lantern of the Steady Harvest)
My rationale: Strategy-> Execution-> Results-> Value that lead to the BrivoTerna name: We put the Lantern of the Steady Harvest.
We deliver value to our customers helping them at defining a good strategy (cyan arrow). 90% of well formulated strategies fail due to poor execution so we also consider strategical execution very important (green arrow). Due to the execution we obtain the results (blue arrow). Finally, the results provide feedback to redefine strategy, and the new strategy has to be executed and new results obtained providing new feedback and on and on. It's like a wheel that finally, must create corporate value: value for shareholders, staholders, employees, providers...-

Target Market(s)

CEOs and steering comitees , invewrnent funds

Industry/Entity Type

Business Consultant

Contact Information for Business Card

Teodoro Vinsquel
CEO & Founder
teodoro.vinsquel@brivoterna-example.com
Mobile: +34 655.803.912
www.brivoterna-example.com

Colors

Designer to choose colors to be used in the design.

Requirements
Nice to have
• Nice to hace the words: Strategy, execution, results
• Nice to vave the claim: Lantern of the Steady Harvest
• The three colors should be shown:
• cyan for STRATEGY
• green for EXECUTION
• blue for RESULTS
Should not have
• Complete black background

```html
<!DOCTYPE html>
<html lang="en">
<head>
<meta charset="utf-8">
<title>BrivoTerna – Business Card</title>
<link href="https://fonts.googleapis.com/css2?family=Montserrat:wght@400;500;600;700&display=swap" rel="stylesheet">
<style>
  :root {
    --backdrop: #3a302c;
    --card: #1c1c1d;
    --white: #ffffff;
    --cyan: #1fa9e6;
    --edge: #1686b8;
    --green: #9cc53c;
    --grey: #d8d8d8;
  }
  * { box-sizing: border-box; margin: 0; padding: 0; }
  html, body {
    width: 1200px; height: 716px; overflow: hidden;
    background: var(--backdrop);
    font-family: "Montserrat", sans-serif;
  }
  .canvas {
    position: relative; width: 1200px; height: 716px;
  }
  .card {
    position: absolute;
    width: 520px; height: 300px;
    top: 208px;
    background: var(--card);
    border-radius: 6px;
  }
  .card-front {
    left: 50px;
    box-shadow: 0 3px 0 var(--edge), 0 6px 0 #125f82, 0 9px 0 var(--edge), 0 18px 30px rgba(0,0,0,.45);
    display: flex; align-items: center; justify-content: center; gap: 14px;
  }
  .card-back {
    left: 630px;
    box-shadow: 0 18px 30px rgba(0,0,0,.45);
  }
  .brand-dot {
    width: 22px; height: 22px; border-radius: 50%;
    background: var(--cyan);
  }
  .brand-name {
    font-weight: 700; color: var(--white);
    font-size: 44px; letter-spacing: -1px;
  }
  .back-brand {
    position: absolute; left: 38px; top: 34px;
    font-size: 38px;
  }
  .contact-group {
    position: absolute; left: 38px;
    border-left: 2px solid var(--green);
    padding-left: 12px;
  }
  .identity { top: 142px; }
  .details { top: 208px; }
  .person-name {
    color: var(--cyan); font-weight: 600; font-size: 22px; line-height: 1.15;
  }
  .person-role {
    color: var(--grey); font-size: 12px; font-weight: 400; margin-top: 2px;
  }
  .detail-line {
    color: var(--white); font-size: 11.5px; line-height: 1.7; white-space: nowrap;
  }
  .detail-label { color: var(--green); font-weight: 600; margin-right: 4px; }
  .detail-gap { display: inline-block; width: 18px; }
  .website { color: var(--cyan); }
</style>
</head>
<body>
<main class="canvas">
  <section class="card card-front" aria-label="Business card front">
    <span class="brand-dot"></span>
    <span class="brand-name">BrivoTerna</span>
  </section>

  <section class="card card-back" aria-label="Business card back">
    <div class="brand-name back-brand">BrivoTerna</div>

    <div class="contact-group identity">
      <div class="person-name">Teodoro Vinsquel</div>
      <div class="person-role">CEO &amp; Founder</div>
    </div>

    <div class="contact-group details">
      <div class="detail-line"><span class="detail-label">P:</span>+34 655.803.912</div>
      <div class="detail-line"><span class="detail-label">E:</span>teodoro.vinsquel@brivoterna-example.com</div>
      <div class="detail-line website">www.brivoterna-example.com</div>
    </div>
  </section>
</main>
</body>
</html>
```